Business card for my new company (Accounting firm)

I need a business card for my new business Brightwell Advisory and Ledger SA. Our services are accounting, tax, audit and financial management. Our customers are small companies, start-ups and new companies. The final design has to show financial security, trust and growth. Please find our logo attached to the business card. Text for the business card: Brightwell Advisory and Ledger SA Tomas Varenholt Director and Founder Certified Accountant Tel. 022 418 57 34 tv@clairevalconseil.ch www.clairevalconseil.ch Rue des Vergières 27 1201 Geneva
Target Market(s)
Our customers are small companies, start-ups and new companies.
Industry/Entity Type
Finance And Accounting
Contact Information for Business Card
Claireval Conseil et Comptes SA
Tomas Varenholt
Directeur et Fondateur
Expert-comptable diplômé
Tél. 022 418 57 34
tv@clairevalconseil.ch
www.clairevalconseil.ch
Rue des Vergières 27
1201 Genève

```html
<!DOCTYPE html>
<html lang="fr">
<head>
<meta charset="utf-8">
<title>Claireval Conseil et Comptes SA – Carte de visite</title>
<link rel="stylesheet" href="https://fonts.googleapis.com/css2?family=Roboto:wght@400;500;700&family=Montserrat:wght@500&display=swap">
<style>
  :root {
    --brand-blue: #1b6595;
    --accent-blue: #2a8fcf;
    --sky-blue: #35abe2;
    --ink: #3a3b3d;
    --paper: #ffffff;
    --backdrop: #e9ebee;
  }
  * { margin: 0; padding: 0; box-sizing: border-box; }
  html, body { width: 1200px; height: 960px; overflow: hidden; }
  body {
    background: var(--backdrop);
    font-family: "Roboto", Arial, sans-serif;
    position: relative;
  }
  .card {
    position: absolute;
    left: 250px;
    width: 700px;
    height: 400px;
    overflow: hidden;
    box-shadow: 0 6px 20px rgba(0,0,0,.18);
  }
  /* Back side */
  .card-back { top: 50px; background: var(--brand-blue); color: var(--paper); }
  .back-brand {
    position: absolute; left: 0; right: 0; top: 130px;
    display: flex; flex-direction: column; align-items: center; gap: 18px;
  }
  .back-mark { width: 64px; height: 64px; border-radius: 50%; background: var(--sky-blue); }
  .back-name {
    font-family: "Montserrat", Arial, sans-serif; font-weight: 500;
    font-size: 26px; letter-spacing: 3px; text-transform: uppercase;
  }
  .back-url { font-size: 17px; letter-spacing: 4px; font-weight: 400; }

  /* Front side */
  .card-front { top: 510px; background: var(--paper); }
  .front-band { position: absolute; inset: 0; }
  .front-brand {
    position: absolute; left: 220px; top: 58px; width: 300px;
    display: flex; flex-direction: column; align-items: center; gap: 12px;
  }
  .front-mark { width: 52px; height: 52px; background: var(--accent-blue); }
  .front-name {
    font-family: "Montserrat", Arial, sans-serif; font-weight: 500;
    color: var(--ink); font-size: 22px; letter-spacing: 2px;
    text-transform: uppercase; text-align: center; line-height: 1.3;
  }
  .holder {
    position: absolute; left: 40px; bottom: 42px; color: var(--paper);
  }
  .holder-name { font-size: 30px; font-weight: 700; margin-bottom: 6px; }
  .holder-role { font-size: 21px; font-weight: 400; line-height: 1.3; }
  .contact {
    position: absolute; left: 452px; top: 222px; color: var(--paper);
    font-size: 17px; line-height: 1.35;
  }
  .contact-address { margin-bottom: 10px; font-style: normal; }
  .contact-row { display: flex; align-items: center; gap: 8px; }
  .contact-row svg { width: 15px; height: 15px; flex: none; fill: var(--paper); }
</style>
</head>
<body>

<section class="card card-back" aria-label="Verso de la carte">
  <div class="back-brand">
    <span class="back-mark"></span>
    <span class="back-name">Claireval</span>
    <span class="back-url">clairevalconseil.ch</span>
  </div>
</section>

<section class="card card-front" aria-label="Recto de la carte">
  <svg class="front-band" viewBox="0 0 700 400" preserveAspectRatio="none" aria-hidden="true">
    <path d="M0 270 L0 400 L700 400 L700 170 L600 170 Q575 170 565 190 Q555 210 530 210 L0 270 Z" fill="var(--brand-blue)"/>
    <path d="M0 258 L530 198 Q552 198 560 180 L566 170 L574 170 Q566 192 548 202 L0 266 Z" fill="var(--sky-blue)"/>
    <path d="M0 258 L230 231 L230 239 L0 266 Z" fill="var(--accent-blue)"/>
  </svg>

  <div class="front-brand">
    <span class="front-mark"></span>
    <span class="front-name">Claireval<br>Conseil et Comptes</span>
  </div>

  <div class="holder">
    <p class="holder-name">Tomas Varenholt</p>
    <p class="holder-role">Directeur et Fondateur<br>Expert-comptable diplômé</p>
  </div>

  <div class="contact">
    <address class="contact-address">Rue des Vergières 27<br>1201 Genève</address>
    <p class="contact-row">
      <svg viewBox="0 0 24 24"><path d="M6.6 10.8a15 15 0 0 0 6.6 6.6l2.2-2.2a1 1 0 0 1 1-.25 11.4 11.4 0 0 0 3.6.6 1 1 0 0 1 1 1V20a1 1 0 0 1-1 1A17 17 0 0 1 3 4a1 1 0 0 1 1-1h3.5a1 1 0 0 1 1 1c0 1.25.2 2.45.6 3.6a1 1 0 0 1-.25 1z"/></svg>
      022 418 57 34
    </p>
    <p class="contact-row">
      <svg viewBox="0 0 24 24"><path d="M2 5h20v14H2z M4 7v.5l8 5 8-5V7l-8 5z" fill-rule="evenodd"/></svg>
      tv@clairevalconseil.ch
    </p>
    <p class="contact-row">
      <svg viewBox="0 0 24 24"><circle cx="12" cy="12" r="10"/><path d="M2 12h20M12 2c3 3 3 17 0 20M12 2c-3 3-3 17 0 20" stroke="#1b6595" stroke-width="1.6" fill="none"/></svg>
      www.clairevalconseil.ch
    </p>
  </div>
</section>

</body>
</html>
```